Business card for builder specialising in renovations.

Need a card for our building business. Business name is under Martin Powles.
Have licence number on card ( 527691K)
Contact number (0400 382 415)
Want to work on logo for some business cards and shirts - something with MP or MPB or open to ideas??
No animations, No hammers. Something sharp and eye catching.
Highlight that we are a renovation specialist. Simple on front with extra details on back with some lines to jot down things.

Target Market(s)

Renovators

Industry/Entity Type

Building

Contact Information for Business Card

2 sided with room on back to jot things down.
Extra details on back so front can be simple ..like, renovations, bathrooms, decks, extensions, new builds,

Logo Text

MP

Font styles to use
Serif

Requirements
Must have
• Eye catching design .
• Name : Martin powles
• Licence number
• Contact number - 0400382415
Nice to have
• Some logo design that we can carry through to other forms of advertising
• Local builder
• Quality work
Should not have
• No animations

```html
<!DOCTYPE html>
<html lang="en">
<head>
<meta charset="utf-8">
<title>Martin Powles – Business Card</title>
<link rel="stylesheet" href="https://fonts.googleapis.com/css2?family=Crimson+Pro:wght@400;600;700&display=swap">
<style>
  :root {
    --page-bg: #2b2b2d;
    --card-bg: #ffffff;
    --brand-blue: #1174bd;
    --ink: #111111;
    --mark: #000000;
  }
  * { box-sizing: border-box; margin: 0; padding: 0; }
  html, body {
    width: 1200px; height: 900px; overflow: hidden;
    background: var(--page-bg);
    font-family: "Crimson Pro", Georgia, serif;
    color: var(--ink);
  }
  .canvas {
    position: relative; width: 1200px; height: 900px;
  }
  .card {
    position: absolute; left: 290px;
    width: 620px; height: 354px;
    background: var(--card-bg);
    border-radius: 22px;
    overflow: hidden;
    box-shadow: 0 12px 30px rgba(0,0,0,.45);
  }
  .card--back { top: 56px; }
  .card--front { top: 470px; }

  /* logo: invented name set in text font, with one plain square */
  .brand-mark {
    display: flex; align-items: center; gap: 12px;
    font-weight: 700; color: var(--mark); line-height: 1;
  }
  .brand-mark__square {
    background: var(--mark);
  }

  /* back side */
  .card--back .brand-mark {
    position: absolute; left: 50%; top: 92px; transform: translateX(-50%);
    font-size: 96px;
  }
  .card--back .brand-mark__square { width: 52px; height: 52px; }
  .services {
    position: absolute; left: 0; right: 0; top: 240px;
    text-align: center; font-size: 17px; letter-spacing: .4px;
    text-transform: uppercase;
  }
  .web-line {
    position: absolute; left: 0; right: 0; top: 272px;
    text-align: center; font-size: 19px;
  }
  .accent { color: var(--brand-blue); }

  /* front side */
  .side-band {
    position: absolute; left: 0; top: 0; bottom: 0; width: 96px;
    background: var(--brand-blue);
  }
  .card--front .logo-tile {
    position: absolute; left: 44px; top: 70px;
    width: 150px; height: 112px; background: var(--card-bg);
    display: flex; align-items: center; justify-content: center;
  }
  .card--front .brand-mark { font-size: 58px; gap: 8px; }
  .card--front .brand-mark__square { width: 30px; height: 30px; }
  .headline {
    position: absolute; left: 214px; right: 24px; top: 74px;
    font-size: 48px; font-weight: 400; color: var(--brand-blue);
    letter-spacing: .5px; line-height: 1; white-space: nowrap;
  }
  .contact {
    position: absolute; left: 330px; top: 188px;
    font-size: 17px; line-height: 1.15;
  }
  .contact__name {
    font-size: 26px; color: var(--brand-blue); font-weight: 400;
    line-height: 1; margin-bottom: 2px;
  }
  .contact__role { margin-bottom: 2px; }
  .contact__row { display: flex; align-items: center; gap: 8px; }
  .contact__row svg { width: 12px; height: 12px; fill: var(--brand-blue); flex: none; }
</style>
</head>
<body>
<main class="canvas">

  <section class="card card--back" aria-label="Card back">
    <div class="brand-mark"><span class="brand-mark__square"></span><span>MP</span></div>
    <p class="services">Renovations, bathrooms, decks, extensions, new builds,</p>
    <p class="web-line">www.<span class="accent">martinpowlesbuild</span>.com</p>
  </section>

  <section class="card card--front" aria-label="Card front">
    <div class="side-band"></div>
    <div class="logo-tile">
      <div class="brand-mark"><span class="brand-mark__square"></span><span>MP</span></div>
    </div>
    <h1 class="headline">MARTIN POWLES</h1>
    <div class="contact">
      <p class="contact__name">MARTIN POWLES</p>
      <p class="contact__role">Director</p>
      <p><span class="accent">Licence:</span> (527691K)</p>
      <p class="contact__row">
        <svg viewBox="0 0 12 12" aria-hidden="true"><path d="M2.5 1l2 2.2-1 1.3a6 6 0 0 0 3.9 3.9l1.3-1 2.2 2-1.2 1.5C5.5 10.6 1.4 6.5.9 2.3z"/></svg>
        <span>0400382415</span>
      </p>
      <p class="contact__row">
        <svg viewBox="0 0 12 12" aria-hidden="true"><path d="M1 2.5h10v7H1zM2 3.5v.3l4 2.6 4-2.6v-.3zM2 5v3.5h8V5L6 7.6z" fill-rule="evenodd"/></svg>
        <span>info@martinpowlesbuild.com</span>
      </p>
      <p class="contact__row">
        <svg viewBox="0 0 12 12" aria-hidden="true"><path d="M6 .8a5.2 5.2 0 1 0 0 10.4A5.2 5.2 0 0 0 6 .8zm0 1.2c.6.7 1 1.7 1.1 3.4H4.9C5 3.7 5.4 2.7 6 2zM2.1 5.4a4 4 0 0 1 1.7-2.7c-.4.8-.8 1.6-.9 2.7zm0 1.2h.8c.1 1.1.5 1.9.9 2.7a4 4 0 0 1-1.7-2.7zM6 10c-.6-.7-1-1.7-1.1-3.4h2.2C7 8.3 6.6 9.3 6 10zm2.2-.7c.4-.8.8-1.6.9-2.7h.8a4 4 0 0 1-1.7 2.7zm.9-3.9c-.1-1.1-.5-1.9-.9-2.7a4 4 0 0 1 1.7 2.7z"/></svg>
        <span>www.<span class="accent">martinpowlesbuild</span>.com</span>
      </p>
    </div>
  </section>

</main>
</body>
</html>
```